CREATE A BUSINESS CARD FOR A BOAT CLEANING SERVICE

WE ARE STARTING A NEW BOAT CLEANING BUSINESS. WE DIVE UNDERWATER TO CLEAN BOAT HULLS, JETTIES, UNDERWATER STRUCTURES ETC. WE ARE LOOKING FOR AN UPPERMARKET MODERN LOGO AND BUSINESS CARD AS ALOT OF OUR TARGET MARKET WILL BE HIGH END. YOU HAVE TO DESIGN A BUSINESS CARD AND LOGO SEPERATELY .
THE BUSINESS CARD DIMESNION MUST BE STANDARD SIZE.
The standard dimensions of a printed business card are 3.5 x 2 inches

Target Market(s)

UNDERWATER SERVICED

Industry/Entity Type

Business

Contact Information for Business Card

HOLLAND UNDERWATER SERVICES

Font styles to use
Serif

Colors

Designer to choose colors to be used in the design.

Requirements
Must have
• HOLLAND
Nice to have
• dark
Should not have
• more than 3 colors

```html
<!DOCTYPE html>
<html lang="en">
<head>
<meta charset="utf-8">
<title>Holland Underwater Services – Business Card</title>
<link href="https://fonts.googleapis.com/css2?family=Lato:wght@300;400;700&display=swap" rel="stylesheet">
<style>
  :root {
    --navy: #0f4f82;
    --grey: #9a9a9a;
    --text-grey: #8a8a8a;
    --white: #ffffff;
    --backdrop: #3b3734;
  }
  * { margin: 0; padding: 0; box-sizing: border-box; }
  html, body { width: 1200px; height: 930px; overflow: hidden; }
  body { background: var(--backdrop); font-family: "Lato", sans-serif; position: relative; }

  .card {
    position: absolute;
    width: 620px;
    height: 354px;
    border-radius: 18px;
    overflow: hidden;
  }
  .card--front { left: 80px; top: 90px; background: var(--navy); }
  .card--back { left: 500px; top: 480px; background: var(--white); }

  .wordmark { position: absolute; text-align: center; }
  .wordmark__name {
    font-weight: 400;
    letter-spacing: 0.55em;
    line-height: 1;
  }
  .wordmark__tagline {
    font-weight: 300;
    letter-spacing: 0.22em;
    margin-top: 10px;
    line-height: 1;
  }
  .card--front .wordmark { left: 0; right: 0; top: 140px; color: var(--white); }
  .card--front .wordmark__name { font-size: 40px; padding-left: 0.55em; }
  .card--front .wordmark__tagline { font-size: 18px; }

  .card--back .wordmark { left: 20px; width: 220px; top: 140px; }
  .card--back .wordmark__name { font-size: 26px; color: var(--navy); padding-left: 0.55em; }
  .card--back .wordmark__tagline { font-size: 11.5px; color: var(--text-grey); margin-top: 8px; }

  .divider {
    position: absolute;
    left: 258px;
    top: 40px;
    width: 1.5px;
    height: 170px;
    background: var(--navy);
  }

  .contact { position: absolute; left: 282px; top: 34px; color: var(--text-grey); }
  .contact__name { font-size: 23px; font-weight: 700; color: var(--navy); letter-spacing: 0.01em; line-height: 1; }
  .contact__title { font-size: 13px; margin-top: 4px; }
  .contact__address { font-size: 13px; line-height: 1.35; margin-top: 6px; padding-left: 16px; }
  .contact__list { list-style: none; margin-top: 6px; font-size: 13px; line-height: 1.4; }
  .contact__list li { display: flex; align-items: center; gap: 7px; }
  .contact__list svg { width: 10px; height: 10px; flex: none; }

  .affiliations {
    position: absolute;
    left: 300px;
    top: 192px;
    display: flex;
    align-items: center;
    gap: 16px;
  }
  .badge { width: 28px; height: 28px; border-radius: 50%; background: var(--navy); opacity: 0.85; }
  .mini-brand { display: flex; align-items: center; gap: 5px; }
  .mini-brand__dot { width: 16px; height: 16px; border-radius: 50%; background: #1c1c1c; }
  .mini-brand__name { font-size: 15px; font-weight: 700; color: #1c1c1c; letter-spacing: 0.02em; }

  .swoosh { position: absolute; left: 0; top: 0; width: 620px; height: 354px; }
</style>
</head>
<body>

  <section class="card card--front" aria-label="Card front">
    <div class="wordmark">
      <div class="wordmark__name">HOLLAND</div>
      <div class="wordmark__tagline">UNDERWATER SERVICE</div>
    </div>
  </section>

  <section class="card card--back" aria-label="Card back">
    <svg class="swoosh" viewBox="0 0 620 354" aria-hidden="true">
      <path d="M0,304 Q350,292 620,160 L620,354 L0,354 Z" fill="var(--grey)"/>
      <path d="M0,309 Q350,298 620,168 L620,354 L0,354 Z" fill="var(--white)"/>
      <path d="M0,314 Q350,305 620,176 L620,354 L0,354 Z" fill="var(--navy)"/>
    </svg>

    <div class="wordmark">
      <div class="wordmark__name">HOLLAND</div>
      <div class="wordmark__tagline">UNDERWATER SERVICE</div>
    </div>

    <div class="divider"></div>

    <div class="contact">
      <div class="contact__name">MARTIN REYES</div>
      <div class="contact__title">President</div>
      <div class="contact__address">410, 318- 9th Ave, SW<br>Calgary, AB T2P 1K4</div>
      <ul class="contact__list">
        <li>
          <svg viewBox="0 0 10 10"><path d="M2,1 L4,1 L4.6,3 L3.5,3.8 Q4.5,5.8 6.2,6.5 L7,5.4 L9,6 L9,8 Q8,9 6.5,8.6 Q2.5,7 1.2,3 Q1,1.8 2,1 Z" fill="var(--navy)"/></svg>
          (555) 214-0398
        </li>
        <li>
          <svg viewBox="0 0 10 10"><rect x="1" y="2" width="8" height="6" fill="none" stroke="var(--navy)" stroke-width="1.2"/><path d="M1,2 L5,5.5 L9,2" fill="none" stroke="var(--navy)" stroke-width="1.2"/></svg>
          info@hollandunderwater.com
        </li>
        <li>
          <svg viewBox="0 0 10 10"><circle cx="5" cy="5" r="4" fill="none" stroke="var(--navy)" stroke-width="1"/><ellipse cx="5" cy="5" rx="1.8" ry="4" fill="none" stroke="var(--navy)" stroke-width="0.8"/><line x1="1" y1="5" x2="9" y2="5" stroke="var(--navy)" stroke-width="0.8"/></svg>
          www.hollandunderwater.com
        </li>
      </ul>
    </div>

    <div class="affiliations">
      <div class="badge" aria-hidden="true"></div>
      <div class="mini-brand">
        <span class="mini-brand__dot" aria-hidden="true"></span>
        <span class="mini-brand__name">HOLLAND</span>
      </div>
    </div>
  </section>

</body>
</html>
```